Brenwick Structures Construction Company Seeking Modern Website

We are a small construction company wanting to create a web presence. We don't have much in the way of current content but will get photos as they come in. Attached is a picture of our business card.
The pages we would like on the menu are:
Home
Portfolio
Product Specs
Testimonials
Our Process
Contact
Some designs we like are:
http://www.tovasheds-example.com/
http://www.qrnstructures-example.com/
http://dunholtbarns-example.com/
http://pellingframes-example.com/
Not much requirements other than that so feel free to be creative!
Updates
Target Market(s)
Construction
Commercial and Residential Buildings
Industry/Entity Type
Construction Company
Number of Pages Required
5+ page
Look and feel

```html
<!DOCTYPE html>
<html lang="en">
<head>
<meta charset="utf-8">
<title>Brenwick Structures</title>
<link href="https://fonts.googleapis.com/css2?family=Lato:ital,wght@0,400;0,700;1,400;1,700&family=Open+Sans:wght@400;600&family=Playball&display=swap" rel="stylesheet">
<style>
:root{
  --blue:#0aa0dc;
  --blue-dark:#0583b8;
  --band:#1f97cc;
  --ink:#3a3a3a;
  --grey:#666;
  --nav:#2b2b2b;
  --footer:#333;
  --red:#d9261c;
}
*{box-sizing:border-box;margin:0;padding:0}
html,body{width:768px;height:1200px;overflow:hidden}
body{position:relative;font-family:"Lato",sans-serif;color:var(--ink);background:#fff}
.abs{position:absolute}

.topbar{left:0;top:0;width:768px;height:24px;background:var(--blue)}
.lang{left:84px;top:5px;width:48px;height:14px;border:1px solid #6cc8ee;color:#fff;font-size:8px;line-height:12px;padding-left:4px}
.social{left:562px;top:0;display:flex}
.social span{width:24px;height:24px;background:var(--blue-dark);border-left:1px solid #0e93c9;display:flex;align-items:center;justify-content:center}
.social span i{display:block;width:8px;height:8px;background:#fff;border-radius:1px}

.header{left:0;top:24px;width:768px;height:60px;background:#fff}
.brand{left:84px;top:42px;display:flex;align-items:center;gap:6px;font-size:22px;font-weight:700;color:var(--blue-dark)}
.brand i{width:14px;height:14px;background:var(--red);display:block}
.callus{right:85px;top:47px;font-size:12px;display:flex;align-items:center;gap:8px}
.callus em{color:#555;font-style:italic}
.callus b{color:var(--blue);font-weight:400;font-size:12px}

.nav{left:0;top:84px;width:768px;height:30px;background:var(--nav)}
.nav ul{position:absolute;left:84px;top:0;display:flex;list-style:none}
.nav li{width:100px;height:30px;color:#fff;font-size:9px;line-height:30px;text-align:center;border-right:1px solid #3c3c3c;text-transform:uppercase}
.nav li.active{background:var(--blue)}

.hero{left:0;top:114px;width:768px;height:330px;background:linear-gradient(160deg,#9fd3ea 0%,#2c8fc2 35%,#6bb7dd 55%,#1a74ad 80%,#a7d6ed 100%)}
.hero h1{position:absolute;left:0;width:768px;top:34px;text-align:center;font-family:"Playball",cursive;font-weight:400;font-size:26px;line-height:33px;color:#fff;text-shadow:0 1px 3px rgba(0,0,0,.4)}
.welcome{left:0;top:332px;width:768px;height:112px;background:rgba(30,160,220,.82);color:#fff;text-align:center}
.welcome h2{margin-top:13px;font-weight:400;font-size:19px;letter-spacing:.2px}
.welcome .rule{width:300px;height:1px;background:rgba(255,255,255,.7);margin:4px auto 0}
.welcome .arrow{width:0;height:0;margin:0 auto;border-left:10px solid transparent;border-right:10px solid transparent;border-top:9px solid #fff}
.welcome p{font-size:9.4px;line-height:13.5px;width:600px;margin:7px auto 0}
.plus{left:368px;top:429px;width:32px;height:15px;background:#333;color:#fff;font-size:15px;line-height:15px;text-align:center;border-radius:2px 2px 0 0}

.card{top:488px;width:185px;height:192px;background:#fff;border:1px solid #e3e3e3;border-top:3px solid var(--blue);box-shadow:0 8px 8px -6px rgba(0,0,0,.25);padding:8px 8px 0}
.card h3{display:flex;align-items:center;gap:8px;font-weight:400;font-size:12.5px;color:var(--blue);text-transform:uppercase}
.card h3 .ic{width:24px;height:24px;border-radius:50%;background:#555;display:flex;align-items:center;justify-content:center}
.photo{margin-top:6px;width:170px;height:73px;background:linear-gradient(90deg,#e3b79a,#f3dccb,#c98d6e);border:1px solid #999}
.card p.txt{font-size:8px;line-height:11.5px;color:#555;margin-top:8px}
.more{position:absolute;right:8px;bottom:6px;font-size:7.5px;font-weight:700;color:var(--blue);display:flex;align-items:center;gap:2px}
.more i{width:7px;height:7px;border-radius:50%;background:#555;display:block}
.item{display:flex;gap:8px;margin-top:8px}
.item svg{flex:none;margin-top:3px}
.item h4{font-weight:400;font-size:9.5px;color:#333}
.item p{font-size:7.8px;line-height:11.5px;color:#555;margin-top:2px}
.know{text-align:right;font-size:7.5px;font-weight:700;color:var(--blue);margin-top:3px}
.dotted{border-top:1px dashed #bbb;margin-top:6px}
.news{display:flex;gap:8px;padding:6px 0 5px;border-bottom:1px dotted #999}
.news:last-of-type{border-bottom:none}
.date{flex:none;width:24px;height:25px;background:#333;color:#fff;text-align:center;border-radius:2px}
.date b{display:block;font-size:9.5px;font-weight:400;line-height:14px}
.date small{display:block;font-size:5.5px;line-height:8px}
.news h4{font-weight:400;font-size:8px;color:#333}
.news p{font-size:7.4px;line-height:11px;color:#555}

.types{left:0;top:724px;width:768px;height:186px;background:var(--band)}
.types h2{position:absolute;top:21px;width:768px;text-align:center;color:#fff;font-weight:400;font-size:14px}
.types .rule{position:absolute;left:234px;top:42px;width:300px;height:1px;background:rgba(255,255,255,.35)}
.tile{top:56px;width:145px;height:102px;border:1px solid #e6e6e6}
.tile .label{position:absolute;left:0;bottom:0;width:100%;height:18px;background:rgba(255,255,255,.85);font-family:"Open Sans",sans-serif;font-weight:600;font-size:10px;line-height:18px;text-align:center;color:#333}
.chev{top:81px}

.say{left:0;top:942px;width:768px;text-align:center}
.say h2{font-family:"Open Sans",sans-serif;font-weight:400;color:var(--red);font-size:19px}
.say p{font-family:"Open Sans",sans-serif;color:#555;font-size:15px;margin-top:-1px}
.quote{left:84px;top:1002px;width:512px;height:64px;border:1px solid #ddd;box-shadow:0 1px 3px rgba(0,0,0,.15);padding:8px 12px;font-style:italic;font-size:8.6px;line-height:15px;color:#444}
.avatar{left:598px;top:998px;width:76px;height:76px;border-radius:50%;border:3px solid #fff;box-shadow:0 0 4px rgba(0,0,0,.35);background:radial-gradient(circle,#d7e6ef,#8fb1c6)}
.who{left:500px;top:1082px;font-style:italic;font-weight:700;font-size:8px;color:#333}

.footer{left:0;top:1123px;width:768px;height:77px;background:var(--footer)}
.fnav{left:85px;top:27px;display:flex;list-style:none}
.fnav li{font-size:7.8px;color:#fff;padding:0 7px;border-left:1px solid #555;line-height:10px}
.fnav li:first-child{padding-left:0;border-left:none;color:var(--blue)}
.ficons{left:496px;top:17px;display:flex;gap:0}
.ficons span{width:26px;height:26px;border-radius:50%;display:flex;align-items:center;justify-content:center;border:2px solid #444}
.fbrand{left:552px;top:19px;font-size:17px;font-weight:700;color:#999}
.copy{right:85px;top:56px;font-size:8px;color:#ddd}
.stripe{left:0;top:1196px;width:768px;height:4px;background:var(--blue)}
</style>
</head>
<body>

<div class="abs topbar"></div>
<div class="abs lang">English &#709;</div>
<div class="abs social" aria-label="Search and social links">
  <span><svg width="10" height="10" viewBox="0 0 10 10"><circle cx="4" cy="4" r="3" fill="none" stroke="#fff" stroke-width="1.5"/><line x1="6.3" y1="6.3" x2="9" y2="9" stroke="#fff" stroke-width="1.5"/></svg></span>
  <span><i></i></span><span><i></i></span><span><i></i></span><span><i></i></span>
</div>

<div class="abs header"></div>
<div class="abs brand"><i></i>Brenwick Structures</div>
<div class="abs callus"><em>Call us TODAY !</em>
  <svg width="11" height="11" viewBox="0 0 24 24"><path fill="#0aa0dc" d="M6.6 10.8a15 15 0 0 0 6.6 6.6l2.2-2.2c.3-.3.7-.4 1-.2 1.1.4 2.3.6 3.6.6.6 0 1 .4 1 1V20c0 .6-.4 1-1 1A17 17 0 0 1 3 4c0-.6.4-1 1-1h3.5c.6 0 1 .4 1 1 0 1.3.2 2.5.6 3.6.1.3 0 .7-.2 1z"/></svg>
  <b>+100 555 0142</b></div>

<nav class="abs nav"><ul>
  <li class="active">Home</li><li>Portfolio</li><li>Product Specs</li><li>Testimonials</li><li>Our Process</li><li>Contact Us</li>
</ul></nav>

<section class="abs hero" role="img" aria-label="Glass office towers seen from below against the sky">
  <h1>Building Dreams, So You Can<br>Build Memories</h1>
</section>
<section class="abs welcome">
  <h2>WELCOME TO BRENWICK STRUCTURES</h2>
  <div class="rule"></div><div class="arrow"></div>
  <p>Lorem ipsum dolor sit amet, consectetur adipiscing elit. Praesent volutpat ultricies euismod. Mauris consectetur tellus quis sem dictum pharetra. Nullam euismod nunc blandit mi sagittis, et posuere nunc iaculis. Aenean in sollicitudin quam, non accumsan ipsum. Vivamus in aliquet ex. Nullam malesuadammodo mi, tristique faucibus nisl condimentum condimentum. Duis porttitor nisi ut elementum so</p>
</section>
<div class="abs plus">+</div>

<article class="abs card" style="left:83px">
  <h3><span class="ic"><svg width="12" height="12" viewBox="0 0 12 12"><circle cx="6" cy="4" r="2.6" fill="#fff"/><path d="M1.5 11a4.5 4 0 0 1 9 0z" fill="#fff"/></svg></span>About Us</h3>
  <div class="photo" role="img" aria-label="Many hands joined together in the middle"></div>
  <p class="txt">Hendrerit in vulputate molestie consquat, sisi atvero eros et accumsan iustoodio dignissimr qui blandit praesent luptatulenit auedolore te feugait nulla facilisilestie conseyat,</p>
  <div class="more">READ MORE <i></i></div>
</article>

<article class="abs card" style="left:292px">
  <h3><span class="ic"><svg width="12" height="12" viewBox="0 0 12 12"><rect x="1.5" y="2.5" width="9" height="8" rx="1" fill="none" stroke="#fff"/><line x1="1.5" y1="5" x2="10.5" y2="5" stroke="#fff"/></svg></span>What We Do</h3>
  <div class="item"><svg width="9" height="8" viewBox="0 0 9 8"><path d="M1 4l2.3 2.3L8 1.5" fill="none" stroke="#3a8f8a" stroke-width="1.8"/></svg>
    <div><h4>Vulputate Molestie Consequat</h4><p>quis nostrud exsetiperj aliquip commod consequa uisquis nostru suscipit nisl roli aliquip exea commod</p></div></div>
  <div class="know">KNOW MORE</div>
  <div class="dotted"></div>
  <div class="item"><svg width="9" height="8" viewBox="0 0 9 8"><path d="M1 4l2.3 2.3L8 1.5" fill="none" stroke="#3a8f8a" stroke-width="1.8"/></svg>
    <div><h4>Vulputate Molestie Consequat</h4><p>quis nostrud exetiperj saliquip commodr consequa uisquis nostru iexetip suscipitt lobtis nisl ut aliquip exea commod</p></div></div>
  <div class="more">KNOW MORE</div>
</article>

<article class="abs card" style="left:499px">
  <h3><span class="ic"><svg width="12" height="12" viewBox="0 0 12 12"><path d="M2 5h2l4-2.5v7L4 7H2z" fill="#fff"/></svg></span>Latest News</h3>
  <div class="news"><div class="date"><b>22</b><small>JULY</small></div><div><h4>Vero eros accumsaet odio</h4><p>quis nostrud exetiperj suscipit lobtis nisl ut aliquip ex ea commod</p></div></div>
  <div class="news"><div class="date"><b>22</b><small>JULY</small></div><div><h4>Eros accumsaet iusto odio</h4><p>quis nostrud exetiperj suscipit lobtfis nisl ut aliquip exea commod</p></div></div>
  <div class="news"><div class="date"><b>22</b><small>JULY</small></div><div><h4>Croeros accumsaet iusto odio</h4><p>quis nostrud exetiperj suscipit lobtisf nisl ut aliquip ex commod</p></div></div>
  <div class="more">READ MORE <i></i></div>
</article>

<section class="abs types">
  <h2>BUILDING TYPES</h2>
  <div class="rule"></div>
  <svg class="abs chev" style="left:68px" width="10" height="16" viewBox="0 0 10 16"><path d="M8 2L2 8l6 6" fill="none" stroke="#8fd0ee" stroke-width="2"/></svg>
  <div class="abs tile" style="left:85px;background:linear-gradient(180deg,#c9ccce 0%,#d6d6d4 45%,#8a7a66 70%,#a5a48a 100%)" role="img" aria-label="Farm shop buildings"><div class="label">Farm Shops</div></div>
  <div class="abs tile" style="left:236px;background:linear-gradient(180deg,#6aa9dc 0%,#9cc6e8 30%,#3f6f7c 50%,#e6dcc6 80%,#efe5d0 100%)" role="img" aria-label="Open machine storage shed"><div class="label">Machine Storage</div></div>
  <div class="abs tile" style="left:387px;background:linear-gradient(180deg,#7fb4e4 0%,#c7d8e6 35%,#eef0ee 55%,#7c9a55 80%,#a8a8a8 100%)" role="img" aria-label="Seed dealership with silos"><div class="label">Seed Dealership</div></div>
  <div class="abs tile" style="left:538px;background:linear-gradient(180deg,#9cc3e0 0%,#5a9a3c 25%,#cfcfcf 50%,#d9b040 80%,#e6d49a 100%)" role="img" aria-label="Long dairy barn"><div class="label">Dairy</div></div>
  <svg class="abs chev" style="left:690px" width="10" height="16" viewBox="0 0 10 16"><path d="M2 2l6 6-6 6" fill="none" stroke="#fff" stroke-width="2"/></svg>
</section>

<section class="abs say">
  <h2>What Our Customers Say</h2>
  <p>Lorem ipsum dolor sit amet consectetur Donec a consequat mag</p>
</section>
<blockquote class="abs quote">&nbsp;&nbsp;&nbsp;&nbsp;&nbsp;&nbsp;&nbsp;Lorem sum dolor sit amet, consectetuer adipiscing elit, sed diam nonummy nibh euismod tincidunt ut laoreet re agn aliquam erat volutpat wisi enim ad minim veniam, quis nostrud exerci tation ullamcorper suscipit lobortis nisl ut aliquip modo conseuatis autem vel eum iriure dolor in hendrerit in vulputate velit esse molestie consequat, vel illum dolore eu.</blockquote>
<div class="abs avatar" role="img" aria-label="Customer portrait"></div>
<div class="abs who">Ravel, Northgate , USA</div>

<footer class="abs footer">
  <ul class="abs fnav"><li>HOME</li><li>PORTFOLIO</li><li>PRODUCT SPACS</li><li>TESTIMONIALS</li><li>OUR PROCESS</li><li>CONTACT US</li></ul>
  <div class="abs ficons">
    <span style="background:var(--blue)"><svg width="9" height="12" viewBox="0 0 9 12"><rect x="1" y="0.5" width="7" height="11" rx="1" fill="none" stroke="#fff"/><circle cx="4.5" cy="9.5" r=".8" fill="#fff"/></svg></span>
    <span style="background:#555"><svg width="12" height="9" viewBox="0 0 12 9"><rect x=".5" y=".5" width="11" height="8" fill="none" stroke="#fff"/><path d="M.5 .5L6 5l5.5-4.5" fill="none" stroke="#fff"/></svg></span>
  </div>
  <div class="abs fbrand">Brenwick Structures</div>
  <div class="abs copy">Copyright © 2015 Brenwick Structures &nbsp;| &nbsp;All Rights Reserved</div>
</footer>
<div class="abs stripe"></div>

</body>
</html>
```